Redesign website for small print company

Vindurgata is a small printing company in Iceland mainly servicing Students, schools, etc. We are also doing all kind of other jobs, like business cards, book printing, brochure printing etc. We are also selling books online.
Our website is: www.vindurgata.is
What we are looking for is:
- Web Design (Uncoded - PSD layout only)
- Mobile friendly design, using our current color scheme: Red, green, yellow and light gray.
- Clean simple design
- Simple, light and easy to use.
- More menu Items/drop down
Industry/Entity Type
Digital Printing
Number of Pages Required
5+ page
Requirements
Must have
- Easy navigation
- Designed for mobile
- Current color scheme (see logo)
Nice to have
- Icon based products

```html
<!DOCTYPE html>
<html lang="en">
<head>
<meta charset="utf-8">
<title>Vindurgata – Printing for students and schools</title>
<link rel="stylesheet" href="https://fonts.googleapis.com/css2?family=Montserrat:wght@400;500;600;700;800&family=Open+Sans:wght@400;600;700;800&display=swap">
<style>
:root{
  --red:#e0231f;
  --green:#0c6a36;
  --leaf:#6aae3a;
  --yellow:#f5c400;
  --yellow-soft:#fbe9a0;
  --gray:#f4f4f4;
  --gray-card:#f1f1f1;
  --ink:#2b2b2b;
  --text:#555;
  --bar:#1f1f1f;
  --foot:#333333;
  --white:#fff;
}
*{box-sizing:border-box;margin:0;padding:0}
html,body{width:1200px;height:3689px;overflow:hidden}
body{font-family:"Open Sans",Arial,sans-serif;color:var(--ink);background:var(--white);position:relative}
.abs{position:absolute}
.head-font{font-family:"Montserrat",Arial,sans-serif}
.btn{display:inline-block;background:var(--green);color:var(--white);font-family:"Montserrat",Arial,sans-serif;font-weight:700;font-size:13px;letter-spacing:.5px;padding:12px 24px;border-radius:3px}
.section-title{position:absolute;left:0;width:1200px;text-align:center;font-family:"Montserrat",Arial,sans-serif;font-weight:700;font-size:24px;color:var(--ink);text-transform:uppercase}
.section-title span{color:var(--red)}

/* top bar */
.topbar{left:0;top:0;width:1200px;height:34px;background:var(--bar);color:#ddd;font-size:11px}
.topbar .lang{left:143px;top:10px;display:flex;align-items:center;gap:8px}
.flag{width:26px;height:14px;background:linear-gradient(#b22 0 50%,#fff 50% 60%,#b22 60%);position:relative}
.flag::before{content:"";position:absolute;left:0;top:0;width:11px;height:8px;background:#2a3f8f}
.topbar .info{right:143px;top:10px;display:flex;gap:22px}
.topbar .info span{display:flex;align-items:center;gap:6px}

/* header */
.header{left:0;top:34px;width:1200px;height:89px;background:var(--white);box-shadow:0 1px 3px rgba(0,0,0,.08)}
.logo{left:143px;top:26px;display:flex;align-items:center;gap:10px}
.logo .mark{width:36px;height:36px;background:var(--red)}
.logo .name{font-family:"Montserrat",Arial,sans-serif;font-weight:800;font-size:25px;color:var(--ink)}
.nav{left:585px;top:38px;display:flex;gap:40px;font-family:"Montserrat",Arial,sans-serif;font-weight:700;font-size:13px}
.nav .active{color:var(--red);border-bottom:2px solid var(--red);padding-bottom:4px}
.tools{left:990px;top:28px;display:flex;align-items:center;gap:24px}
.cart{width:34px;height:34px;border:2px solid var(--green);border-radius:50%;display:flex;align-items:center;justify-content:center}

/* hero */
.hero{left:0;top:123px;width:1200px;height:475px;background:linear-gradient(180deg,#f7f7f7,#d7d7d7)}
.hero .art{left:130px;top:20px;width:330px;height:420px;border-radius:12px;background:linear-gradient(135deg,#f2c400 0 30%,#d52a20 30% 55%,#2a74c0 55% 78%,#59a93a 78%);opacity:.85}
.hero .copy{left:480px;top:110px}
.hero .l1{font-family:"Open Sans",Arial,sans-serif;font-size:68px;font-weight:600;line-height:1;color:#333}
.hero .l1 b{color:var(--leaf);font-weight:800}
.hero .l2{font-family:"Open Sans",Arial,sans-serif;font-size:68px;font-weight:800;line-height:1.05;color:#333}
.hero .l3{font-size:31px;font-weight:600;color:#333;margin-top:6px}
.dots{left:576px;top:565px;display:flex;gap:6px}
.dots i{width:11px;height:11px;border-radius:50%;border:2px solid #999;display:block}
.dots i.on{background:var(--green);border-color:var(--green)}

/* products */
.product{width:281px;height:195px;background:var(--gray-card);display:flex;flex-direction:column;align-items:center;justify-content:center;gap:22px}
.product.hover{background:var(--white);box-shadow:0 2px 10px rgba(0,0,0,.15)}
.product .ic{width:80px;height:80px;border-radius:50%;background:var(--yellow-soft);display:flex;align-items:center;justify-content:center}
.product .lbl{font-family:"Montserrat",Arial,sans-serif;font-weight:700;font-size:16px}

/* about */
.about{left:0;top:1217px;width:1200px;height:516px;background:var(--gray)}
.photo{border-radius:2px}
.about .text{left:644px;top:62px;width:413px}
.about .kicker{font-family:"Montserrat",Arial,sans-serif;font-weight:700;font-size:20px;color:var(--red)}
.about h2{font-family:"Montserrat",Arial,sans-serif;font-weight:700;font-size:26px;margin:4px 0 16px}
.about p{font-size:13px;line-height:22px;color:var(--text);margin-bottom:12px}

/* steps */
.step{width:260px;text-align:center}
.step .circle{width:120px;height:120px;margin:0 auto;position:relative}
.step .num{position:absolute;left:-2px;bottom:6px;width:32px;height:32px;border-radius:50%;background:var(--yellow);font-weight:700;font-size:16px;display:flex;align-items:center;justify-content:center}
.step h3{font-family:"Montserrat",Arial,sans-serif;font-weight:700;font-size:15px;margin-top:20px}
.step p{font-size:12px;line-height:18px;color:#444;margin-top:4px}

/* offers */
.offers{left:0;top:2193px;width:1200px;height:495px;background:linear-gradient(135deg,#f6d000,#e9b900 50%,#f8d93a)}
.offer{top:123px;height:303px;overflow:hidden}
.offer-left{left:143px;width:442px;background:#f2f2f2}
.offer-left .art{left:215px;top:80px;width:215px;height:150px;background:linear-gradient(120deg,#e8e8e8,#c73c3c 40%,#3a7bc4 60%,#f2c400);transform:rotate(-14deg)}
.offer-left .copy{left:24px;top:52px}
.offer .pct{font-family:"Montserrat",Arial,sans-serif;font-weight:800;font-size:34px;color:var(--red);line-height:1.1}
.offer .get{font-family:"Montserrat",Arial,sans-serif;font-weight:800;font-size:32px;color:var(--ink);line-height:1.1}
.offer .sub{font-family:"Montserrat",Arial,sans-serif;font-weight:500;font-size:22px;color:#555;line-height:1.2;margin-bottom:18px}
.offer-right{left:615px;width:442px;background:linear-gradient(135deg,#4a2a5e,#8a2f6b 45%,#d4c9c0 75%,#7a6a8a)}
.offer-right .panel{left:50px;top:62px;width:342px;height:180px;background:rgba(30,20,35,.75);text-align:center;padding-top:26px}
.offer-right .get{color:var(--white)}
.offer-right .sub{color:#eee;font-size:19px}

/* reviews */
.review{top:2816px;width:281px;height:167px;background:var(--gray-card);padding:22px 22px}
.review .top{display:flex;justify-content:space-between;font-weight:600;font-size:14px}
.stars{color:var(--yellow);letter-spacing:1px;font-size:14px}
.review p{font-size:12px;line-height:18px;color:#555;margin-top:12px}
.person{top:3008px;display:flex;align-items:center;gap:14px}
.avatar{width:50px;height:50px;border-radius:50%;background:linear-gradient(#c9c3bd,#7d756f)}
.person b{display:block;color:var(--red);font-size:13px}
.person small{font-size:12px;color:#444}
.arrow-side{top:2886px}

/* features band */
.band{left:0;top:3197px;width:1200px;height:118px;background:var(--green);color:var(--white)}
.feature{top:32px;display:flex;align-items:center;gap:14px}
.feature .ic{width:56px;height:56px;border-radius:50%;background:var(--white);display:flex;align-items:center;justify-content:center}
.feature b{display:block;font-family:"Montserrat",Arial,sans-serif;font-size:14px}
.feature small{font-size:12px}

/* footer */
.footer{left:0;top:3315px;width:1200px;height:374px;background:var(--foot);color:#ddd}
.signup{left:143px;top:46px;width:332px;height:246px;background:var(--white);padding:28px 20px;color:var(--ink)}
.signup h4{font-family:"Montserrat",Arial,sans-serif;font-weight:700;font-size:19px;color:var(--red)}
.signup h4 span{color:var(--ink)}
.signup p{font-size:12px;line-height:17px;color:#666;margin:8px 0 14px}
.signup .field{height:38px;border:1px solid #ccc;font-size:11px;color:#999;padding:11px 12px;margin-bottom:16px}
.signup .btn{font-size:12px;padding:10px 16px}
.fcol h5{font-family:"Montserrat",Arial,sans-serif;font-weight:700;font-size:13px;color:var(--white);margin-bottom:14px}
.fcol li{list-style:none;font-size:12px;line-height:21px}
.fcol li::before{content:"›";margin-right:8px}
.pay{display:flex;gap:6px;margin-top:4px}
.pay i{width:30px;height:18px;background:#eee;border-radius:2px;display:block}
.contact div{display:flex;gap:8px;align-items:flex-start;font-size:12px;line-height:17px;margin-bottom:12px}
.copyright{left:143px;top:342px;font-size:11px;color:#bbb}
.social{right:143px;top:335px;display:flex;gap:6px}
.social i{width:22px;height:22px;border-radius:50%;display:block}
</style>
</head>
<body>

<!-- top bar -->
<div class="abs topbar">
  <div class="abs lang">LANGUAGE <span class="flag"></span>
    <svg width="8" height="6" viewBox="0 0 8 6"><path d="M0 0h8L4 5z" fill="#ccc"/></svg></div>
  <div class="abs info">
    <span><svg width="12" height="12" viewBox="0 0 24 24"><path d="M6.6 10.8a15 15 0 006.6 6.6l2.2-2.2c.3-.3.7-.4 1-.2 1.1.4 2.3.6 3.6.6.6 0 1 .4 1 1V20c0 .6-.4 1-1 1A17 17 0 013 4c0-.6.4-1 1-1h3.5c.6 0 1 .4 1 1 0 1.3.2 2.5.6 3.6.1.3 0 .7-.2 1z" fill="#ddd"/></svg>555 0142</span>
    <span><svg width="13" height="10" viewBox="0 0 26 20"><rect x="1" y="1" width="24" height="18" fill="none" stroke="#ddd" stroke-width="2"/><path d="M1 1l12 10L25 1" fill="none" stroke="#ddd" stroke-width="2"/></svg>verk@vindurgata.is</span>
    <span><svg width="12" height="12" viewBox="0 0 24 24"><circle cx="12" cy="12" r="10" fill="none" stroke="#ddd" stroke-width="2"/><path d="M12 6v6l4 3" fill="none" stroke="#ddd" stroke-width="2"/></svg>Mon - Fri: 9-17</span>
  </div>
</div>

<!-- header -->
<div class="abs header">
  <div class="abs logo"><span class="mark"></span><span class="name">VINDURGATA</span></div>
  <nav class="abs nav"><span class="active">HOME</span><span>SERVICES</span><span>JOB SUBMIT</span><span>ABOUT US</span></nav>
  <div class="abs tools">
    <svg width="16" height="16" viewBox="0 0 24 24"><circle cx="10" cy="10" r="7" fill="none" stroke="#222" stroke-width="3"/><path d="M15 15l7 7" stroke="#222" stroke-width="3"/></svg>
    <span class="cart"><svg width="16" height="16" viewBox="0 0 24 24"><path d="M2 4h3l3 11h11l2-8H7" fill="none" stroke="#e0231f" stroke-width="2.5"/><circle cx="9" cy="19" r="1.8" fill="#e0231f"/><circle cx="17" cy="19" r="1.8" fill="#e0231f"/></svg></span>
  </div>
</div>

<!-- hero -->
<section class="abs hero">
  <div class="abs art" role="img" aria-label="Figure fitting the last piece into a coloured jigsaw puzzle block"></div>
  <div class="abs copy">
    <div class="l1">WANT TO <b>BRAND</b></div>
    <div class="l2">YOUR BUSINESS?</div>
    <div class="l3">We can help brand your business effectively</div>
  </div>
  <div class="abs dots"><i></i><i class="on"></i><i></i></div>
</section>

<!-- products -->
<h2 class="section-title" style="top:660px"><span>Our</span> Products</h2>
<div class="abs product hover" style="left:143px;top:720px">
  <div class="ic"><svg width="40" height="40" viewBox="0 0 40 40"><rect x="10" y="6" width="20" height="28" fill="none" stroke="#e0231f" stroke-width="2.5"/><path d="M14 14h12M14 19h12M14 24h8" stroke="#e0231f" stroke-width="2"/></svg></div>
  <div class="lbl">ESSAYS</div></div>
<div class="abs product" style="left:457px;top:720px">
  <div class="ic"><svg width="40" height="40" viewBox="0 0 40 40"><rect x="6" y="10" width="28" height="20" fill="none" stroke="#e0231f" stroke-width="2.5"/><circle cx="14" cy="19" r="3" fill="#e0231f"/><path d="M21 17h9M21 22h9" stroke="#e0231f" stroke-width="2"/></svg></div>
  <div class="lbl">BUSINESS CARDS</div></div>
<div class="abs product" style="left:777px;top:720px">
  <div class="ic"><svg width="40" height="40" viewBox="0 0 40 40"><path d="M6 10l9-3 10 3 9-3v23l-9 3-10-3-9 3z" fill="none" stroke="#e0231f" stroke-width="2.5"/><path d="M15 7v23M25 10v23" stroke="#e0231f" stroke-width="2"/></svg></div>
  <div class="lbl">LEAFLETS</div></div>
<div class="abs product" style="left:143px;top:952px">
  <div class="ic"><svg width="40" height="40" viewBox="0 0 40 40"><rect x="9" y="12" width="20" height="22" fill="none" stroke="#e0231f" stroke-width="2.5"/><path d="M13 12V7h18v22h-2" fill="none" stroke="#e0231f" stroke-width="2"/><path d="M13 19h12M13 24h12" stroke="#e0231f" stroke-width="2"/></svg></div>
  <div class="lbl">BOOK PRINTING</div></div>
<div class="abs product" style="left:457px;top:952px">
  <div class="ic"><svg width="40" height="40" viewBox="0 0 40 40"><rect x="9" y="6" width="22" height="28" fill="none" stroke="#e0231f" stroke-width="2.5"/><rect x="13" y="11" width="14" height="9" fill="#e0231f"/><path d="M13 25h14M13 29h9" stroke="#e0231f" stroke-width="2"/></svg></div>
  <div class="lbl">POSTERS</div></div>
<div class="abs product" style="left:777px;top:952px">
  <div class="ic"><svg width="40" height="40" viewBox="0 0 40 40"><rect x="8" y="6" width="24" height="28" fill="none" stroke="#e0231f" stroke-width="2.5"/><path d="M13 6v28" stroke="#e0231f" stroke-width="2"/><rect x="17" y="12" width="10" height="7" fill="none" stroke="#e0231f" stroke-width="2"/></svg></div>
  <div class="lbl">TEXTBOOKS</div></div>

<!-- about -->
<section class="abs about">
  <div class="abs photo" style="left:143px;top:70px;width:355px;height:236px;background:linear-gradient(135deg,#e9ecef,#9aa6b2 45%,#445a70)" role="img" aria-label="Team working around a table covered in printed layouts"></div>
  <div class="abs photo" style="left:340px;top:232px;width:258px;height:164px;background:linear-gradient(120deg,#f2d23a,#d83b7a 40%,#3a8fd0 70%,#222)" role="img" aria-label="Colour swatch fan and printed colour charts"></div>
  <div class="abs text">
    <div class="kicker">ABOUT US</div>
    <h2>WELCOME TO UNIVERSITY</h2>
    <p>University education is a company located in the campus, which has specialized in the service of school staff, as well as providing general public printing.</p>
    <p>Higher education publishes seminars and first-class textbooks for courses, prints theses for lesson, as well as working on an unprecedented number of smaller pieces for students, teachers and organizations. These include brochures, reports, questionnaires, business cards, books, OCR scanning and more.</p>
    <p>Higher education is a tailored print shop, The Heron is the official eco-label of the Nordic countries, which has created a foothold in this country and is known among consumers.</p>
    <span class="btn" style="margin-top:8px">READ MORE</span>
  </div>
</section>

<!-- how it works -->
<h2 class="section-title" style="top:1798px"><span>How we make</span> printing as easy</h2>
<svg class="abs" style="left:393px;top:1905px" width="130" height="40" viewBox="0 0 130 40"><path d="M4 30 Q60 0 118 18" fill="none" stroke="#999" stroke-width="1.5" stroke-dasharray="4 3"/><path d="M112 12l8 7-10 3" fill="none" stroke="#999" stroke-width="1.5"/></svg>
<svg class="abs" style="left:713px;top:1905px" width="130" height="40" viewBox="0 0 130 40"><path d="M4 30 Q60 0 118 18" fill="none" stroke="#999" stroke-width="1.5" stroke-dasharray="4 3"/><path d="M112 12l8 7-10 3" fill="none" stroke="#999" stroke-width="1.5"/></svg>

<div class="abs step" style="left:150px;top:1858px">
  <div class="circle"><svg width="120" height="120" viewBox="0 0 120 120"><path d="M20 95A52 52 0 1 1 100 95" fill="none" stroke="#0c6a36" stroke-width="3"/><path d="M52 40v34l-6-6-6 4 14 18h22l6-20-14-6V40a5 5 0 00-16 0z" fill="none" stroke="#e0231f" stroke-width="3"/><path d="M48 30a14 14 0 0120 0" fill="none" stroke="#e0231f" stroke-width="2.5"/></svg><span class="num">1</span></div>
  <h3>SELECT OPTIONS</h3><p>Lorem ipsum dolor sit amet contuer<br>adiping elit sed diam noummy.</p></div>
<div class="abs step" style="left:470px;top:1858px">
  <div class="circle"><svg width="120" height="120" viewBox="0 0 120 120"><path d="M20 95A52 52 0 1 1 100 95" fill="none" stroke="#0c6a36" stroke-width="3"/><path d="M42 28h26l12 12v50H42z" fill="none" stroke="#e0231f" stroke-width="3"/><path d="M49 50h24M49 58h24M49 66h16" stroke="#e0231f" stroke-width="2.5"/><circle cx="78" cy="86" r="9" fill="#e0231f"/><path d="M78 91v-9M74 85l4-4 4 4" stroke="#fff" stroke-width="2" fill="none"/></svg><span class="num">2</span></div>
  <h3>UPLOAD YOUR DESIGN</h3><p>Lorem ipsum dolor sit amet contuer<br>adiping elit sed diam noummy.</p></div>
<div class="abs step" style="left:790px;top:1858px">
  <div class="circle"><svg width="120" height="120" viewBox="0 0 120 120"><path d="M20 95A52 52 0 1 1 100 95" fill="none" stroke="#0c6a36" stroke-width="3"/><path d="M30 44h9l8 30h32l7-22H43" fill="none" stroke="#e0231f" stroke-width="3"/><circle cx="52" cy="84" r="4" fill="#e0231f"/><circle cx="74" cy="84" r="4" fill="#e0231f"/><path d="M62 34l6 6 12-14" fill="none" stroke="#e0231f" stroke-width="3"/></svg><span class="num">3</span></div>
  <h3>CHECKOUT &amp; ORDER</h3><p>Lorem ipsum dolor sit amet contuer<br>adiping elit sed diam noummy.</p></div>
<span class="abs btn" style="left:537px;top:2083px">GET STARTED</span>

<!-- offers -->
<section class="abs offers">
  <h2 class="section-title" style="top:62px"><span>Offers</span> and deals</h2>
  <div class="abs offer offer-left">
    <div class="abs art" role="img" aria-label="Stack of colourful printed business cards"></div>
    <div class="abs copy">
      <div class="pct">25% OFF</div>
      <div class="get">GET YOUR</div>
      <div class="sub">CUSTOMIZED<br>ESSAYS</div>
      <span class="btn">GET NOW</span>
    </div>
  </div>
  <div class="abs offer offer-right" role="img" aria-label="Fanned printed magazine and book covers">
    <div class="abs panel">
      <div class="get">GET YOUR</div>
      <div class="sub">CUSTOMIZED BOOK PRINTING</div>
      <span class="btn">GET NOW</span>
    </div>
  </div>
</section>

<!-- reviews -->
<h2 class="section-title" style="top:2756px"><span>Client</span> Reviews</h2>
<svg class="abs arrow-side" style="left:90px" width="16" height="30" viewBox="0 0 16 30"><path d="M13 2L3 15l10 13" fill="none" stroke="#bbb" stroke-width="2"/></svg>
<svg class="abs arrow-side" style="left:1094px" width="16" height="30" viewBox="0 0 16 30"><path d="M3 2l10 13L3 28" fill="none" stroke="#bbb" stroke-width="2"/></svg>

<div class="abs review" style="left:143px"><div class="top">Lorem ipsum dolor <span class="stars">★★★★★</span></div>
  <p>Lorem ipsum dolor amet consetuer adipcing elit sed diam nonummy nibh euismod tidunt ut laoreet dolre magna aliquam erat volut. Ut wisi enim ad minim veniam.</p></div>
<div class="abs review" style="left:457px"><div class="top">Lorem ipsum dolor <span class="stars">★★★★★</span></div>
  <p>Lorem ipsum dolor amet consetuer adipcing elit sed diam nonummy nibh euismod tidunt ut laoreet dolre magna aliquam erat volut. Ut wisi enim ad minim veniam.</p></div>
<div class="abs review" style="left:777px"><div class="top">Lorem ipsum dolor <span class="stars">★★★★★</span></div>
  <p>Lorem ipsum dolor amet consetuer adipcing elit sed diam nonummy nibh euismod tidunt ut laoreet dolre magna aliquam erat volut. Ut wisi enim ad minim veniam.</p></div>

<div class="abs person" style="left:163px"><span class="avatar" role="img" aria-label="Client portrait"></span><span><b>Daniel Hart</b><small>(Lorem Ipsum)</small></span></div>
<div class="abs person" style="left:477px"><span class="avatar" role="img" aria-label="Client portrait"></span><span><b>Lena Marsh</b><small>(Lorem Ipsum)</small></span></div>
<div class="abs person" style="left:797px"><span class="avatar" role="img" aria-label="Client portrait"></span><span><b>Oskar Reed</b><small>(Lorem Ipsum)</small></span></div>
<span class="abs btn" style="left:538px;top:3086px">VIEW ALL</span>

<!-- features band -->
<section class="abs band">
  <div class="abs feature" style="left:143px"><span class="ic"><svg width="30" height="22" viewBox="0 0 30 22"><rect x="1" y="3" width="17" height="12" fill="#0c6a36"/><path d="M18 7h6l4 5v3H18z" fill="#0c6a36"/><circle cx="7" cy="17" r="3" fill="#0c6a36"/><circle cx="23" cy="17" r="3" fill="#0c6a36"/></svg></span>
    <span><b>FREE SHIPPING &amp; RETURN</b><small>Free shipping on all orders over $99.</small></span></div>
  <div class="abs feature" style="left:497px"><span class="ic"><svg width="34" height="34" viewBox="0 0 34 34"><circle cx="17" cy="17" r="14" fill="none" stroke="#0c6a36" stroke-width="3"/><text x="17" y="24" text-anchor="middle" font-family="Open Sans,sans-serif" font-weight="700" font-size="19" fill="#0c6a36">$</text></svg></span>
    <span><b>MONEY BACK GUARANTEE</b><small>100% money back guarantee.</small></span></div>
  <div class="abs feature" style="left:827px"><span class="ic"><svg width="34" height="34" viewBox="0 0 34 34"><circle cx="17" cy="17" r="14" fill="none" stroke="#0c6a36" stroke-width="3" stroke-dasharray="70 18"/><path d="M17 9v8l5 4" fill="none" stroke="#0c6a36" stroke-width="2.5"/></svg></span>
    <span><b>ONLINE SUPPORT 24/7</b><small>Lorem ipsum dolor sit amet.</small></span></div>
</section>

<!-- footer -->
<footer class="abs footer">
  <div class="abs signup">
    <h4>SIGN UP <span>TODAY !</span></h4>
    <p>Lorem ipsum dolor sit laoreet dolore magnutpat quis nostrud exerci tation.</p>
    <div class="field">Your Email Address...</div>
    <span class="btn">SUBSCRIBE!</span>
  </div>
  <div class="abs fcol" style="left:510px;top:52px">
    <h5>QUICK LINKS</h5>
    <ul><li>Home</li><li>Services</li><li>Job Submit</li><li>About Us</li></ul>
    <h5 style="margin-top:14px;margin-bottom:8px">PAYMENTS OPTIONS</h5>
    <div class="pay"><i></i><i></i><i></i><i></i><i></i></div>
  </div>
  <div class="abs fcol" style="left:730px;top:52px">
    <h5>CAN WE HELP YOU?</h5>
    <ul><li>Your Account</li><li>Shipping &amp; Handling</li><li>Refunds &amp; Returns</li><li>Stockists</li><li>Privacy Policy</li><li>Terms &amp; Condition</li><li>Sitemap</li></ul>
  </div>
  <div class="abs fcol contact" style="left:907px;top:52px;width:160px">
    <h5>CONTACT DETAILS</h5>
    <div><svg width="11" height="14" viewBox="0 0 12 16"><path d="M6 0a6 6 0 00-6 6c0 4.5 6 10 6 10s6-5.5 6-10a6 6 0 00-6-6z" fill="#ddd"/><circle cx="6" cy="6" r="2.2" fill="#333"/></svg><span>Lindargata 14, 101 Reykjavík,<br>Vsk: 410592</span></div>
    <div><svg width="12" height="12" viewBox="0 0 24 24"><path d="M6.6 10.8a15 15 0 006.6 6.6l2.2-2.2c.3-.3.7-.4 1-.2 1.1.4 2.3.6 3.6.6.6 0 1 .4 1 1V20c0 .6-.4 1-1 1A17 17 0 013 4c0-.6.4-1 1-1h3.5c.6 0 1 .4 1 1 0 1.3.2 2.5.6 3.6.1.3 0 .7-.2 1z" fill="#ddd"/></svg><span>555 0142</span></div>
    <div><svg width="12" height="12" viewBox="0 0 24 24"><rect x="3" y="8" width="18" height="12" fill="#ddd"/><rect x="6" y="3" width="12" height="5" fill="#ddd"/></svg><span>555 0142</span></div>
    <div><svg width="12" height="12" viewBox="0 0 24 24"><circle cx="12" cy="12" r="10" fill="none" stroke="#ddd" stroke-width="2.5"/><path d="M7 9l5 4 5-4" fill="none" stroke="#ddd" stroke-width="2"/></svg><span>verk@vindurgata.is</span></div>
  </div>
  <div class="abs copyright">Copyright © 2018 Vindurgata . All Rights Reserved.</div>
  <div class="abs social"><i style="background:#3b5b98"></i><i style="background:#3aa1e0"></i><i style="background:#1e77b5"></i><i style="background:#d34836"></i><i style="background:#b0476b"></i></div>
</footer>

</body>
</html>
```